W. Darrow Billboard

2 miles ahead on right
Voted number 1 ... again!
California cuisine
Located in Historic Marbury Hill Inn
Picture of a couple dining
www.torvellis.com 555.317.2968

Target Market(s)

travelers

Industry/Entity Type

hospitality

Font styles to use
Serif

Colors
59FF00
82FF00
B8FF75
E3FFCB
F4FFEA
EE7325
F08F49
F5BC92
FAE3D3
FDF4ED

Requirements
Should not have
• bright colors

```html
<!DOCTYPE html>
<html lang="en">
<head>
<meta charset="utf-8">
<title>Torvelli's Southwest Bar &amp; Grill — Billboard</title>
<link rel="stylesheet" href="https://fonts.googleapis.com/css2?family=Fraunces:wght@700;900&family=Roboto+Slab:wght@800&family=Roboto+Condensed:wght@700&family=Open+Sans:wght@400&display=swap">
<style>
  :root {
    --lime-deep: #5aa51a;
    --lime: #82d11f;
    --lime-light: #b8ff75;
    --lime-pale: #e3ffcb;
    --orange: #ee7325;
    --ink: #3a3a3a;
    --grey: #333333;
    --white: #ffffff;
    --badge-red: #b3202a;
    --gold: #d9a441;
  }
  html, body {
    margin: 0;
    width: 1200px;
    height: 801px;
    overflow: hidden;
    background: #ececec;
  }
  .billboard {
    position: relative;
    width: 1200px;
    height: 801px;
    background: var(--white);
    overflow: hidden;
    font-family: "Open Sans", sans-serif;
  }
  .billboard__shapes {
    position: absolute;
    inset: 0;
  }
  .brand {
    position: absolute;
    left: 48px;
    top: 30px;
    margin: 0;
    color: var(--orange);
    font-family: "Fraunces", serif;
    font-weight: 900;
    line-height: 1;
  }
  .brand__name {
    display: block;
    font-size: 150px;
    letter-spacing: 1px;
  }
  .brand__sub {
    display: block;
    margin-top: 6px;
    margin-left: 150px;
    font-size: 34px;
    letter-spacing: 4px;
    text-transform: uppercase;
  }
  .tagline {
    position: absolute;
    left: 100px;
    top: 300px;
    margin: 0;
    font-family: "Fraunces", serif;
    font-weight: 700;
    font-size: 60px;
    line-height: 1.1;
    color: var(--lime-deep);
    text-shadow: 2px 2px 0 rgba(0,0,0,0.25);
  }
  .cuisine {
    position: absolute;
    left: 30px;
    top: 395px;
    width: 595px;
    height: 78px;
    border-radius: 39px;
    background: linear-gradient(180deg, var(--lime-light), var(--lime) 55%, var(--lime-deep));
    box-shadow: 3px 4px 6px rgba(0,0,0,0.25);
    display: flex;
    align-items: center;
    justify-content: center;
    font-family: "Roboto Slab", serif;
    font-weight: 800;
    font-size: 46px;
    letter-spacing: 3px;
    color: var(--white);
    text-shadow: -2px -2px 0 var(--ink), 2px -2px 0 var(--ink), -2px 2px 0 var(--ink), 2px 2px 0 var(--ink);
  }
  .location {
    position: absolute;
    left: 200px;
    top: 500px;
    margin: 0;
    font-size: 32px;
    line-height: 1.2;
    color: var(--grey);
  }
  .contact {
    position: absolute;
    margin: 0;
    font-family: "Roboto Condensed", sans-serif;
    font-weight: 700;
    line-height: 1;
    color: var(--white);
    text-shadow: 2px 3px 3px rgba(0,0,0,0.45);
  }
  .contact--phone {
    left: 28px;
    top: 596px;
    font-size: 72px;
    letter-spacing: 3px;
  }
  .contact--web {
    left: 410px;
    top: 692px;
    font-size: 50px;
    letter-spacing: 1px;
  }
  .directions {
    position: absolute;
    left: 34px;
    top: 708px;
    margin: 0;
    font-family: "Fraunces", serif;
    font-weight: 700;
    font-size: 28px;
    line-height: 1.2;
    color: var(--lime-pale);
  }
  .award {
    position: absolute;
    left: 640px;
    top: 392px;
    width: 150px;
    height: 250px;
    text-align: center;
  }
  .award__label {
    font-family: "Fraunces", serif;
    font-weight: 700;
    font-size: 19px;
    line-height: 1.2;
    color: var(--ink);
  }
  .dining-photo {
    position: absolute;
    left: 845px;
    top: 278px;
    width: 355px;
    height: 523px;
  }
</style>
</head>
<body>
  <main class="billboard">
    <svg class="billboard__shapes" width="1200" height="801" viewBox="0 0 1200 801" aria-hidden="true">
      <defs>
        <linearGradient id="band-fill" x1="0" y1="0" x2="0" y2="1">
          <stop offset="0" stop-color="#9be23a"/>
          <stop offset="1" stop-color="#5aa51a"/>
        </linearGradient>
      </defs>
      <path class="footer-band" d="M0 580 L560 580 Q590 580 600 610 L610 660 L1200 660 L1200 801 L0 801 Z" fill="url(#band-fill)"/>
      <path class="photo-frame" d="M1200 250 L890 250 Q818 250 818 330 Q818 520 875 801 L1200 801 Z" fill="var(--lime)"/>
    </svg>

    <h1 class="brand">
      <span class="brand__name">Torvelli's</span>
      <span class="brand__sub">Southwest Bar &amp; Grill</span>
    </h1>

    <p class="tagline">Good Food, Good Life</p>
    <div class="cuisine">California Cuisine</div>
    <p class="location">Historic Marbury Hill Inn</p>

    <div class="award">
      <div class="award__label">Voted Number</div>
      <svg width="150" height="210" viewBox="0 0 170 238" aria-hidden="true">
        <polygon points="55,120 30,215 60,195 80,220 92,130" fill="var(--gold)"/>
        <polygon points="115,120 140,215 110,195 90,220 78,130" fill="var(--gold)"/>
        <circle cx="85" cy="80" r="72" fill="var(--gold)"/>
        <circle cx="85" cy="80" r="62" fill="var(--badge-red)"/>
        <text x="85" y="98" text-anchor="middle" font-family="Fraunces, serif" font-weight="900" font-size="70" fill="#f5d27a">1</text>
        <text x="85" y="128" text-anchor="middle" font-family="Fraunces, serif" font-weight="700" font-size="18" fill="#ffffff">again!</text>
      </svg>
    </div>

    <p class="contact contact--phone">555.317.2968</p>
    <p class="directions">2 miles ahead on right</p>
    <p class="contact contact--web">www.torvellis.com</p>

    <svg class="dining-photo" viewBox="0 0 355 523" role="img" aria-label="Photo of a smiling couple dining at a white-clothed table with champagne glasses">
      <defs>
        <linearGradient id="photo-fill" x1="0" y1="0" x2="0" y2="1">
          <stop offset="0" stop-color="#f7f7f7"/>
          <stop offset="0.5" stop-color="#dedede"/>
          <stop offset="1" stop-color="#f2f2f2"/>
        </linearGradient>
      </defs>
      <path d="M355 0 L50 0 Q0 0 0 70 Q0 260 50 523 L355 523 Z" fill="url(#photo-fill)"/>
    </svg>
  </main>
</body>
</html>
```